Business card design Needed for new logo / Construction business, home extensions and new builds

We need a business card design using our new logo files which i will attach to this project :)

We are a small construction business specialising in home extensions, new builds and property development. We are very ambitious and would appreciate professional and elegant designs for our new business card.

Very serious about using the services on MakerQuarry and recently acquired our new logo from here :)

Please get involved, i will feedback when i can as i am very busy but can respond daily, thanks

Target Market(s)

People that want to build onto their houses, new building developments or adding too their existing property

Industry/Entity Type

Construction

Contact Information for Business Card

Renwick Tolliver Construction, Lionel Ashby (Managing Director), Tel 07822254961, email - info@renwick-tolliver, www.renwick-tolliver.co.uk

Colors

Designer to choose colors to be used in the design.

Requirements
Must have
• I like a deep grey on the back please. A lot of you have provided black from and back, try mixing things up a little. The black looks cool 😎 Thanks

```html
<!DOCTYPE html>
<html lang="en">
<head>
<meta charset="utf-8">
<title>Renwick Tolliver Construction – Business Card</title>
<link rel="stylesheet" href="https://fonts.googleapis.com/css2?family=Cinzel:wght@500;600&family=Crimson+Text:wght@400;600&display=swap">
<style>
  :root {
    --stage: #8a8a8a;
    --card-black: #0b0b0b;
    --card-deep: #1a1a1a;
    --card-mid: #2a2a2a;
    --gold: #c9962e;
    --gold-soft: #8a6a25;
    --silver: #d6d6d6;
    --ink-light: #e8e8e8;
  }
  * { margin: 0; padding: 0; box-sizing: border-box; }
  html, body {
    width: 1200px; height: 900px; overflow: hidden;
    background: var(--stage);
  }
  .stage {
    position: relative; width: 1200px; height: 900px;
  }
  .card {
    position: absolute; left: 260px; width: 680px; height: 400px;
    border-radius: 30px; overflow: hidden;
    box-shadow: 0 14px 30px rgba(0,0,0,0.35);
  }
  /* Back side */
  .card--back { top: 34px; background: var(--card-deep); }
  .back-pattern {
    position: absolute; inset: 0;
    background: radial-gradient(ellipse at 55% 40%, var(--card-mid) 0%, var(--card-deep) 55%, var(--card-black) 100%);
  }
  .back-mark {
    position: absolute; right: 70px; top: 120px;
    display: flex; align-items: center; gap: 8px;
    font-family: "Cinzel", serif; font-weight: 600; font-size: 15px;
    letter-spacing: 1px; color: var(--gold);
  }
  .back-mark .dot { width: 10px; height: 10px; background: var(--gold); }
  /* Front side */
  .card--front { top: 466px; background: var(--card-black); }
  .front-emblem {
    position: absolute; left: 0; top: 0; width: 330px; height: 400px;
    background: linear-gradient(160deg, #1c1c1c 0%, #171309 55%, var(--card-black) 100%);
  }
  .wordmark {
    position: absolute; right: 60px; top: 70px; text-align: center;
    font-family: "Cinzel", serif; font-weight: 600; color: var(--silver);
    letter-spacing: 1px;
  }
  .wordmark .line-1 { font-size: 34px; line-height: 1.1; }
  .wordmark .line-2 { font-size: 22px; letter-spacing: 3px; }
  .contact {
    position: absolute; left: 150px; right: 60px; bottom: 40px;
    font-family: "Crimson Text", serif; color: var(--ink-light);
  }
  .rule { height: 1px; background: linear-gradient(90deg, var(--gold-soft), var(--gold), var(--gold-soft)); }
  .person { padding: 14px 0 12px; }
  .person-name {
    font-family: "Cinzel", serif; font-weight: 500; font-size: 26px;
    color: var(--gold); letter-spacing: 1px; line-height: 1.1;
  }
  .person-role { font-size: 19px; }
  .sep { color: var(--gold); padding: 0 6px; }
  .web { font-size: 18px; padding-top: 10px; }
</style>
</head>
<body>
<main class="stage">
  <section class="card card--back" aria-label="Card back">
    <div class="back-pattern" role="img" aria-label="Subtle tone-on-tone repeating brand pattern across the back of the card"></div>
    <div class="back-mark"><span class="dot"></span>Renwick Tolliver</div>
  </section>

  <section class="card card--front" aria-label="Card front">
    <div class="front-emblem" role="img" aria-label="Large faint brand emblem in dark grey and muted gold"></div>
    <div class="wordmark">
      <div class="line-1">RENWICK TOLLIVER</div>
      <div class="line-2">CONSTRUCTION</div>
    </div>
    <div class="contact">
      <div class="rule"></div>
      <div class="person">
        <div class="person-name">LIONEL ASHBY</div>
        <div class="person-role">Managing Director<span class="sep">|</span>P. 07822254961</div>
      </div>
      <div class="rule"></div>
      <div class="web">E. info@renwick-tolliver.co.uk<span class="sep">|</span>W. www.renwick-tolliver.co.uk</div>
    </div>
  </section>
</main>
</body>
</html>
```